Marlowe Group needs a business card

I would like the card to be simple but modern and elegant.
I like black and white.
or black and gold.
we are a private finance lender and also are involved in property and property developments.

please look at the business card photos i provided i would like M.G only one one side and all the other details on the other side use fonts that tie in with my theme.

Industry/Entity Type

Finance

Contact Information for Business Card

Marlowe Group (M.G) Daniel Marlowe M: 0413586207 E: danmarl@inboxmail.test

Font styles to use
Other font styles liked:
• Use fonts that would reflect our business

Colors
000000
ffffff

Requirements
Must have
• one side of details
• other side has either M.G or Marlowe Group like in the photos provided

```html
<!DOCTYPE html>
<html lang="en">
<head>
<meta charset="utf-8">
<title>Marlowe Group – Business Card</title>
<link rel="stylesheet" href="https://fonts.googleapis.com/css2?family=Open+Sans:wght@400;700&display=swap">
<style>
  :root {
    --backdrop: #6b4a33;
    --card-white: #ffffff;
    --ink: #111111;
    --ink-soft: #555555;
    --rule: #333333;
    --band-black: #000000;
    --band-grey: #6d6d6d;
    --card-black: #0b0b0b;
    --texture-tone: #1c1c1c;
    --gold: #c9a63a;
  }
  * { margin: 0; padding: 0; box-sizing: border-box; }
  html, body { width: 1200px; height: 987px; overflow: hidden; }
  body {
    background: var(--backdrop);
    font-family: "Open Sans", Arial, sans-serif;
    position: relative;
  }
  .card {
    position: absolute;
    left: 293px;
    width: 615px;
    height: 352px;
    box-shadow: 0 3px 10px rgba(0,0,0,0.35);
    overflow: hidden;
  }
  .card-front { top: 130px; background: var(--card-white); }
  .card-back  { top: 505px; background: var(--card-black); }

  .brand {
    position: absolute;
    right: 34px;
    top: 66px;
    display: flex;
    align-items: center;
    gap: 10px;
  }
  .brand-mark {
    width: 14px; height: 14px;
    background: var(--ink);
  }
  .brand-name {
    font-weight: 700;
    font-size: 30px;
    letter-spacing: 1px;
    color: var(--ink);
    text-transform: uppercase;
  }

  .holder-name {
    position: absolute;
    left: 27px;
    top: 226px;
    font-size: 21px;
    font-weight: 700;
    color: var(--ink);
  }
  .divider {
    position: absolute;
    left: 27px;
    right: 34px;
    top: 262px;
    height: 1px;
    background: var(--rule);
  }
  .contact {
    position: absolute;
    left: 27px;
    top: 273px;
    font-size: 16px;
    line-height: 24px;
    color: var(--ink-soft);
  }
  .contact .label { font-weight: 700; color: var(--ink); }
  .website {
    position: absolute;
    right: 34px;
    top: 292px;
    font-size: 16px;
    color: var(--ink-soft);
  }
  .footer-bands {
    position: absolute;
    left: 0; bottom: 0;
    width: 615px; height: 13px;
  }

  .texture {
    position: absolute;
    inset: 0;
    background: linear-gradient(180deg, var(--texture-tone), var(--card-black));
  }
  .monogram {
    position: absolute;
    inset: 0;
    display: flex;
    align-items: center;
    justify-content: center;
    font-weight: 700;
    font-size: 104px;
    letter-spacing: 4px;
    color: var(--gold);
  }
</style>
</head>
<body>
  <section class="card card-front" aria-label="Business card front">
    <div class="brand">
      <span class="brand-mark"></span>
      <span class="brand-name">Marlowe Group</span>
    </div>
    <h1 class="holder-name">Daniel Marlowe</h1>
    <div class="divider"></div>
    <p class="contact">
      <span class="label">Cell :</span> 0413586207<br>
      danmarl@inboxmail.test
    </p>
    <p class="website">www.marlowegroup.test</p>
    <svg class="footer-bands" viewBox="0 0 615 13" aria-hidden="true">
      <polygon points="0,0 387,0 382,13 0,13" fill="var(--band-black)"/>
      <polygon points="392,2 615,2 615,13 387,13" fill="var(--band-grey)"/>
    </svg>
  </section>

  <section class="card card-back" aria-label="Business card back">
    <div class="texture" role="img" aria-label="Dark repeating monogram texture"></div>
    <div class="monogram">M.G</div>
  </section>
</body>
</html>
```